COMPANY NAME: Bright Harbor Ventures: Task Description: We are a new UK based business with global rea

Target Market

- Personal and professional development – 30-55 age group, corporate leaders, Eastern European and Asian markets
- On-assignment projects – Corporate market – Eastern European and Asian Markets
- Property investment - 35-65 age group, Europe, USA, Australia

What we need

We need logos and brand design for a suite of web platforms (website, twitter and Facebook profile). We would like to have a cohesive and consistent look across all of our online platforms. The design suite must therefore include social media logos, backgrounds and headers. Specifically we are looking for:

a. Facebook header/page design: likely to have a more youthful look

b. Website: Header, background and layout that is responsive to devices, iPhone primarily, then tablet, then PC (we have purchased a website building package from SiteKettle so if you are familiar with one of their themes, it would be great to have a design that fits with a theme you would recommend); Design should be able to accommodate a place to position video in the medium term but an image in the short term.

c. LinkedIn: header/logo; more corporate look

d. Twitter: background/logo

e. Powerpoint template: background and logo - simple and soft background not busy

f. Electronic Newsletter: logo, header and sidebar; simple and soft background not busy

h. Business card: sophisticated and simple

Colors

We have in mind a preference for colors from the purple family, maybe lavender, so as to appeal to all genders and age groups. Though we are happy to go with a recommendation if you think otherwise.

We would like a look that is professional, airy, bright, fresh, futuristic, insightful, friendly.

Ethos of the brand

- experiencing opportunity and being fulfilled in a changing world
- services are facilitated through insights
- support provided through our product, services and tailored approach to coaching/partnerships (which includes private client match-making)
- we are service providers and passionate about quality and modern leadership skills at all stages in life.

The company name is "Bright Harbor Ventures” - our main message is helping people move to the next level - through investments, personal and professional growth.

Some of our messaging

1. International Leadership in a new world.

2. New technology;

3. Informed;

4. Positively Influential

5. Making a difference;

6. Empowered;

7. Risk free investments;

8. Commercial opportunity;

9. Fulfilled living;

10. Carefree and Fun Living;

11. Progression;

12. Open-minded

13. Energy/dynamic

The Business:
The business is to move people very quickly out of situations that hold them back. the situations could be their own personal situations; their career; their jobs; their teams; their ideas; their finances; their financial opportunities. Remove their fears and give them the strategies to take action. The team are international and have 40 years experience between them in this area.

We do want to come across modern and dynamic, customer outcome focussed, building long-term relationships; international.
Updates

Project Deadline Extended
Reason: We have not found the right designs - we are not just looking for a website design but also images and logos. Most images we can see in the designs are stock images - very standard. We need an image which will be the face of the company, like the shop front window. This main image will be used on social media (top image) and also the home page of the website.

Target Market(s)

30-55 years
Eastern Europe; UK; Asia; Africa; Middle East
Personal, Professional, Corporate, and Financial Growth

Industry/Entity Type

Business Service

Contact Information for Business Card

Simple and stylish
the 3 areas of the business on the reverse -

International look - Offices in UK and San Francisco

Company name
web address www.brightharborventure.com
email director@brightharborventure.com
Facebook bright harbor venture
LinkedIn Bright Harbor Venture
Twitter Bright Harbor Venture
Telephone: +44 (0) 768 213 5597

Logo Text

Something that symbolises unlimited growth - probably not text - could use the word INSIGHT in some way

Number of Pages Required

1 page

Colors
e4daeb
f3f1f8
ffffff

Requirements
Must have
• social media symbols and address
• company name
• Melanie Thorpe
• Director
• Telephone +44 (0) 768 213 5597
• Website name www.brightharborventure.co.uk
• Reverse of Card:
• Discreet, Fast, Bright Harbor Consultancy
• Corporate, Professional, Personal & Property Investment
Nice to have
• not too angular; soft lines; not too cluttered (possibly social media on the reverse and just logo, name, number on the front?
Should not have
• too busy

```html
<!DOCTYPE html>
<html lang="en">
<head>
<meta charset="utf-8">
<title>Bright Harbor Venture — Professional and Personal Consultancy</title>
<link rel="stylesheet" href="https://fonts.googleapis.com/css2?family=Open+Sans:wght@300;400;600&display=swap">
<style>
  :root {
    --lavender: #e4daeb;
    --lavender-deep: #c9bcd6;
    --mist: #f3f1f8;
    --white: #ffffff;
    --ink: #2f2f33;
    --ink-soft: #5d5d63;
    --ink-muted: #7a7a80;
    --icon: #4e4d55;
    --rule: rgba(255,255,255,0.55);
  }
  * { box-sizing: border-box; margin: 0; padding: 0; }
  html, body { width: 1200px; height: 2532px; overflow: hidden; }
  body {
    position: relative;
    background: var(--white);
    font-family: "Open Sans", Arial, sans-serif;
    color: var(--ink);
  }
  .page { position: relative; width: 1200px; height: 2532px; overflow: hidden; }
  .abs { position: absolute; }

  /* Hero */
  .hero { left: 0; top: 0; width: 1200px; height: 565px; overflow: hidden; }
  .hero-photo {
    position: absolute; inset: 0;
    background:
      radial-gradient(ellipse at 30% 35%, #efe9e6 0%, rgba(239,233,230,0) 45%),
      radial-gradient(ellipse at 85% 55%, #a9c6dc 0%, rgba(169,198,220,0) 55%),
      linear-gradient(100deg, #b9c4cf 0%, #dcdde2 35%, #eceef2 60%, #b7cfe0 100%);
  }
  .brand { left: 111px; top: 34px; display: flex; align-items: center; gap: 12px; }
  .brand-mark { width: 46px; height: 46px; border-radius: 50%; background: var(--ink); flex: none; }
  .brand-name {
    font-weight: 600; font-size: 19px; line-height: 23px; letter-spacing: 0.5px;
    text-transform: uppercase; color: var(--ink);
  }
  .menu-toggle { left: 1012px; top: 51px; display: flex; align-items: center; gap: 8px;
    font-size: 13px; font-weight: 600; color: var(--ink); text-transform: uppercase; }
  .hero-rule { left: 200px; width: 800px; height: 1px; background: var(--rule); }
  .hero-title {
    left: 0; width: 1200px; top: 381px; text-align: center;
    font-weight: 300; font-size: 37px; letter-spacing: -0.3px; color: var(--ink);
    text-transform: uppercase;
  }
  .slider-dots { left: 582px; top: 530px; display: flex; gap: 8px; }
  .slider-dots span { width: 8px; height: 8px; border-radius: 50%; background: rgba(255,255,255,0.7); }
  .slider-dots span.is-active { background: var(--ink); }

  /* Section headings */
  .section-title {
    left: 0; width: 1200px; text-align: center;
    font-weight: 300; font-size: 29px; text-transform: uppercase; color: var(--ink);
  }

  /* Welcome */
  .welcome-lead { left: 0; width: 1200px; top: 715px; text-align: center; font-size: 17px; color: var(--ink); }
  .welcome-copy {
    left: 136px; width: 930px; top: 755px; text-align: center;
    font-size: 12px; line-height: 26px; color: var(--ink-soft);
  }

  /* Features */
  .features-band { left: 0; top: 942px; width: 1200px; height: 498px; background: var(--lavender); }
  .watch-link { left: 0; width: 1200px; top: 1048px; display: flex; justify-content: center; align-items: center; gap: 10px; font-size: 16px; color: var(--ink); }
  .video-frame {
    left: 184px; top: 1105px; width: 832px; height: 443px;
    background: var(--white); padding: 4px;
    box-shadow: 0 14px 18px -10px rgba(0,0,0,0.28);
  }
  .video-still {
    position: relative; width: 100%; height: 100%;
    background:
      radial-gradient(ellipse at 50% 50%, #b98f79 0%, rgba(185,143,121,0) 30%),
      radial-gradient(ellipse at 92% 40%, #2b2f3a 0%, rgba(43,47,58,0) 35%),
      linear-gradient(110deg, #e3ebe9 0%, #cfdcd9 45%, #dfe6e4 75%, #9fa8ad 100%);
  }
  .play-button { position: absolute; left: 375px; top: 178px; }

  /* Services */
  .service { top: 1734px; width: 320px; }
  .service-badge {
    width: 130px; height: 130px; border-radius: 50%;
    background: radial-gradient(circle at 50% 35%, #ece6f0 0%, var(--lavender) 55%, var(--lavender-deep) 100%);
    display: flex; align-items: center; justify-content: center;
  }
  .service-title { margin-top: 32px; font-weight: 300; font-size: 20px; text-transform: uppercase; color: var(--ink); }
  .service-list { list-style: none; margin-top: 20px; }
  .service-list li { font-size: 13px; line-height: 34px; color: var(--ink-soft); display: flex; align-items: center; gap: 10px; }
  .service-list li::before { content: "»"; font-size: 13px; color: var(--ink-soft); }

  /* Footer */
  .site-footer { left: 0; top: 2132px; width: 1200px; height: 310px; background: var(--mist); }
  .footer-heading { font-weight: 300; font-size: 19px; text-transform: uppercase; color: var(--ink); top: 2180px; }
  .footer-text { font-size: 12px; line-height: 26px; color: var(--ink-muted); }
  .contact-row { left: 111px; display: flex; align-items: center; gap: 14px; font-size: 15px; font-weight: 600; color: var(--ink-soft); }
  .contact-icon { width: 40px; height: 40px; border-radius: 50%; background: radial-gradient(circle at 50% 35%, #ece6f0, var(--lavender-deep)); display: flex; align-items: center; justify-content: center; }
  .quick-links { left: 516px; top: 2218px; list-style: none; }
  .quick-links li { font-size: 12px; line-height: 29px; color: var(--ink-muted); }
  .newsletter-form { left: 768px; top: 2321px; width: 305px; height: 47px; background: var(--white); border: 1px solid #e2dde8; display: flex; align-items: center; padding-left: 16px; }
  .newsletter-form .placeholder { flex: 1; font-size: 12px; color: var(--ink-muted); }
  .newsletter-submit { width: 44px; height: 35px; margin-right: 5px; background: var(--lavender-deep); display: flex; align-items: center; justify-content: center; }

  /* Bottom bar */
  .bottom-bar { left: 0; top: 2442px; width: 1200px; height: 90px; background: var(--lavender); }
  .copyright { left: 111px; top: 2476px; font-size: 12px; color: var(--ink-soft); }
  .connect { left: 888px; top: 2473px; display: flex; align-items: center; gap: 8px; font-size: 12px; color: var(--ink-soft); }
  .connect-dot { width: 26px; height: 26px; border-radius: 50%; background: #5b5960; }
</style>
</head>
<body>
<div class="page">

  <header class="hero abs">
    <div class="hero-photo" role="img" aria-label="Photograph of three colleagues smiling while reviewing documents together in a bright office"></div>
    <div class="brand abs">
      <span class="brand-mark"></span>
      <span class="brand-name">Bright Harbor<br>Venture</span>
    </div>
    <div class="menu-toggle abs">
      <svg width="18" height="14" viewBox="0 0 18 14"><rect width="18" height="2.4" fill="#2f2f33"/><rect y="5.8" width="18" height="2.4" fill="#2f2f33"/><rect y="11.6" width="18" height="2.4" fill="#2f2f33"/></svg>
      Menu
    </div>
    <div class="hero-rule abs" style="top:338px"></div>
    <h1 class="hero-title abs">Professional and Personal Consultancy</h1>
    <div class="hero-rule abs" style="top:478px"></div>
    <div class="slider-dots abs"><span class="is-active"></span><span></span></div>
  </header>

  <section class="welcome">
    <h2 class="section-title abs" style="top:657px">Welcome to Bright Harbor Venture</h2>
    <p class="welcome-lead abs">Hello and welcome to the company that works with you on your terms.</p>
    <p class="welcome-copy abs">If you seek an experienced and trusted partner to work with you on an assignment or simply want some strategies to move your personal or professional talents to the next level then you are in the right place. If you feel that the pace of change in business is so fast that to be an outstanding leader you should ensure you are brought up to speed regularly then you are in the right place. If you are hearing about the essential new leadership essentials and you are ready to hear how to adopt them into your life or business then you are at the right place. I am so convinced that you will be delighted with how fast you can make change happen.</p>
  </section>

  <section class="features">
    <div class="features-band abs"></div>
    <h2 class="section-title abs" style="top:990px">Our Features</h2>
    <div class="watch-link abs">
      <svg width="15" height="15" viewBox="0 0 16 16"><circle cx="8" cy="8" r="8" fill="#2f2f33"/><path d="M6 4.5 L11.5 8 L6 11.5 Z" fill="#e4daeb"/></svg>
      Watch Our Video
    </div>
    <div class="video-frame abs">
      <div class="video-still" role="img" aria-label="Video still of a business person touching a glowing digital chart interface">
        <svg class="play-button" width="74" height="74" viewBox="0 0 74 74"><circle cx="37" cy="37" r="35" fill="rgba(90,90,95,0.55)" stroke="rgba(255,255,255,0.75)" stroke-width="3"/><path d="M29 22 L53 37 L29 52 Z" fill="#ffffff"/></svg>
      </div>
    </div>
  </section>

  <section class="services">
    <h2 class="section-title abs" style="top:1642px">What We Do?</h2>

    <div class="service abs" style="left:111px">
      <div class="service-badge">
        <svg width="72" height="52" viewBox="0 0 72 52"><path d="M2 14 L18 6 L36 14 L54 6 L70 14 L70 28 L56 34 L40 46 Q36 49 32 46 L14 32 L2 28 Z" fill="#4e4d55"/><path d="M22 22 L36 14 L46 20" stroke="#e4daeb" stroke-width="3" fill="none"/></svg>
      </div>
      <h3 class="service-title">Consultancy</h3>
      <ul class="service-list">
        <li>Professional and Personal</li>
        <li>Next Generation Leaders (16-30)</li>
        <li>Consultation Options</li>
      </ul>
    </div>

    <div class="service abs" style="left:462px">
      <div class="service-badge">
        <svg width="60" height="54" viewBox="0 0 60 54"><rect x="4" y="36" width="9" height="16" fill="#4e4d55"/><rect x="18" y="28" width="9" height="24" fill="#4e4d55"/><rect x="32" y="32" width="9" height="20" fill="#4e4d55"/><rect x="46" y="18" width="9" height="34" fill="#4e4d55"/><path d="M4 28 L20 14 L34 22 L52 4" stroke="#4e4d55" stroke-width="4" fill="none"/><path d="M44 2 L56 0 L54 12 Z" fill="#4e4d55"/></svg>
      </div>
      <h3 class="service-title">On Assignment</h3>
      <ul class="service-list">
        <li>Team Cohesion Strategy</li>
        <li>Go To Market Strategy</li>
        <li>Internationalisation Strategy</li>
      </ul>
    </div>

    <div class="service abs" style="left:797px">
      <div class="service-badge">
        <svg width="46" height="58" viewBox="0 0 46 58"><rect x="2" y="2" width="42" height="54" rx="3" fill="none" stroke="#4e4d55" stroke-width="3.5"/><rect x="9" y="10" width="28" height="3" fill="#4e4d55"/><rect x="9" y="17" width="28" height="3" fill="#4e4d55"/><rect x="9" y="24" width="20" height="3" fill="#4e4d55"/><path d="M10 46 L18 36 L24 42 L36 32" stroke="#4e4d55" stroke-width="3" fill="none"/></svg>
      </div>
      <h3 class="service-title">Property: Private Client</h3>
      <ul class="service-list">
        <li>Promotion and cash-buyer matching</li>
        <li>Investment: high return projects</li>
        <li>Commercial: Hotels and Senior Housing</li>
        <li>Prestige Residential: US, Australia, UK</li>
      </ul>
    </div>
  </section>

  <footer>
    <div class="site-footer abs"></div>

    <h4 class="footer-heading abs" style="left:111px">Contact Us</h4>
    <p class="footer-text abs" style="left:111px; top:2218px; width:300px">Let's chat, if you want a non committal conversation get in touch by email or telephone.</p>
    <div class="contact-row abs" style="top:2289px">
      <span class="contact-icon"><svg width="16" height="16" viewBox="0 0 16 16"><path d="M3 1 L6 1 L7 5 L5 6.5 Q6.5 9.5 9.5 11 L11 9 L15 10 L15 13 Q14 15 12 15 Q2 13 1 3 Q1 1 3 1 Z" fill="#4e4d55"/></svg></span>
      +44 (0) 768 213 5597
    </div>
    <div class="contact-row abs" style="top:2346px">
      <span class="contact-icon"><svg width="16" height="12" viewBox="0 0 16 12"><rect x="1" y="1" width="14" height="10" fill="none" stroke="#4e4d55" stroke-width="1.6"/><path d="M1 1 L8 7 L15 1" fill="none" stroke="#4e4d55" stroke-width="1.6"/></svg></span>
      Director@brightharborventure.com
    </div>

    <h4 class="footer-heading abs" style="left:516px">Quick Links</h4>
    <ul class="quick-links abs">
      <li>About You</li>
      <li>About Us</li>
      <li>Our Values</li>
      <li>Testimonials</li>
      <li>Social Media</li>
      <li>News Alert</li>
    </ul>

    <h4 class="footer-heading abs" style="left:768px">Signup Our Newsletter</h4>
    <p class="footer-text abs" style="left:768px; top:2218px; width:305px">Lorem ipsum dolor sit amet, consectetur adipiscing elit. Aliquam in feugiat magna. Proin eu semper sem, vel effi citur dolor. Donec non posuere mi.</p>
    <div class="newsletter-form abs">
      <span class="placeholder">Email Address</span>
      <span class="newsletter-submit"><svg width="16" height="14" viewBox="0 0 16 14"><path d="M1 7 H12 M7 2 L12 7 L7 12" stroke="#3a3940" stroke-width="3" fill="none"/></svg></span>
    </div>

    <div class="bottom-bar abs"></div>
    <p class="copyright abs">Copyrights © 2016 Bright Harbor Venture. All Right Reserved.</p>
    <div class="connect abs">
      <span style="margin-right:6px">Connect Us :</span>
      <span class="connect-dot"></span>
      <span class="connect-dot"></span>
      <span class="connect-dot"></span>
      <span class="connect-dot"></span>
    </div>
  </footer>

</div>
</body>
</html>
```